Commercial Real Estate for Lease Listing Flyer

I am looking to put together a flyer for our available office space in our building. It needs to look professional and it will be standard sized 8.5 x 11 and double sided. Full color as well. This flyer will need to be able to be put in a PDF and a picture file that can be embedded in an email. I have included pictures, logo, and a Word document with the information you should need. Also, I included a bunch of SAMPLE leasing flyers that you can get ideas from. The floor plan is also included in here. I want it specifically noted that the top suite is Suite 100 and the bottom suite is 120. And list their size as well. I will be reviewing all designs very quickly, so be sure to check the comments.

• Please refer to these links for additional photos:
• "Twilight 1.jpg" at: https://files.plinthdocs.net/a/preview/3f7d1a92-b4e0-4c1a-8e5f-71c0d2ab9e34
• Twilight 2_straightened.jpg" at: https://files.plinthdocs.net/a/preview/a15c8e03-7d2b-4f9e-b6a1-0c93e4f72d58
• "Twilight 3.jpg" at: https://files.plinthdocs.net/a/preview/6e2b9f71-c3a4-4d08-9e7b-5f1a8c03d6e2
• "Twilight 4.jpg" at: https://files.plinthdocs.net/a/preview/c84a0d6e-1f3b-4e57-a2c9-9b7e05f4d813
• "Twilight 5.jpg" at: https://files.plinthdocs.net/a/preview/7b0f5c28-e6d1-4a93-8f4e-d25a1b6c07f9
• "Twilight 6.jpg" at: https://files.plinthdocs.net/a/preview/e3c6a417-5b92-4f0d-bc8e-4a1f97d2e065
• "Twilight 7.jpg" at: https://files.plinthdocs.net/a/preview/5a9d2e80-c7f4-4b16-93a0-e8b6f1c4d27a
• "Twilight 8.jpg" at: https://files.plinthdocs.net/a/preview/b2e7f069-84c3-4d5a-a71e-3c0d9b58f6e4
• "Twilight 9.jpg" at: https://files.plinthdocs.net/a/preview/4d8c1b3f-a0e5-4f72-8b69-f17e2c05a9d3
• "Twilight 10.jpg" at: https://files.plinthdocs.net/a/preview/f09a6c52-3e18-4b7d-9c24-6b5d80e1f3a7
• "Twilight 11.jpg" at: https://files.plinthdocs.net/a/preview/8e4f2d06-b9c7-4a31-85e0-d7a3c16f4b92

```html
<!DOCTYPE html>
<html lang="en">
<head>
<meta charset="utf-8">
<title>Hale Road Centre – Sublease Flyer</title>
<link href="https://fonts.googleapis.com/css2?family=Montserrat:wght@400;600;700;800;900&family=Lato:wght@400;700;900&display=swap" rel="stylesheet">
<style>
:root{
  --stage:#8a8a8a;
  --red:#e8393a;
  --red-deep:#d92f31;
  --ink:#1f1f1f;
  --black:#1b1b1b;
  --paper:#ececec;
  --white:#ffffff;
  --photo-a:#b99a63;
  --photo-b:#5b4032;
  --plan:#f4f4f4;
}
*{box-sizing:border-box;margin:0;padding:0}
html,body{width:1200px;height:1200px;overflow:hidden;background:var(--stage)}
body{position:relative;font-family:"Lato",sans-serif;color:var(--ink)}
.page{position:absolute;overflow:hidden;box-shadow:0 2px 6px rgba(0,0,0,.35)}
.page--front{left:28px;top:249px;width:557px;height:720px;background:var(--paper)}
.page--back{left:615px;top:243px;width:561px;height:726px;background:var(--white)}
.abs{position:absolute}
.front-shapes{position:absolute;left:0;top:0;width:557px;height:720px}

.headline{left:18px;top:255px;font-family:"Montserrat",sans-serif;font-weight:800;line-height:1}
.headline .kicker{font-size:19px;color:var(--ink);letter-spacing:.3px}
.headline .name{font-size:52px;font-weight:900;color:var(--red);margin-top:3px;letter-spacing:-.5px}
.headline .sub{font-size:23px;font-weight:900;color:var(--red);margin-top:2px}
.address{left:18px;top:356px;width:240px;font-size:13px;font-weight:700;line-height:16px;color:var(--ink)}

.brand-front{left:344px;top:285px;display:flex;align-items:center;gap:8px;color:var(--white);font-family:"Lato",sans-serif;font-size:18px;font-weight:400}
.brand-dot{width:18px;height:18px;border-radius:50%;background:var(--white)}

.thumb{position:absolute;width:144px;height:103px;background:linear-gradient(160deg,#c8a766,#6a4a36)}

.about{left:332px;top:421px;width:220px;font-family:"Montserrat",sans-serif;font-weight:900;color:var(--red);line-height:1}
.about .small{font-size:17px}
.about .big{font-size:31px;margin-top:1px}
.facts{left:332px;top:478px;width:222px;list-style:none;font-size:11.6px;line-height:15px;color:var(--ink)}
.facts li{position:relative;padding-left:11px;margin-bottom:3px}
.facts li::before{content:"";position:absolute;left:0;top:4px;width:5px;height:3px;border-left:1.6px solid var(--red);border-bottom:1.6px solid var(--red);transform:rotate(-45deg)}
.facts li.note{padding-left:26px}
.facts li.note::before{left:14px;top:5px;width:0;height:0;border:3px solid transparent;border-left:5px solid var(--red);transform:none}
.facts b{font-weight:900}

.foot-contact{left:20px;top:680px;display:flex;gap:8px;color:var(--white);font-size:9.5px;font-weight:700;line-height:12px}
.foot-phone{left:228px;top:688px;display:flex;align-items:center;gap:6px;color:var(--white);font-family:"Lato",sans-serif;font-weight:700;font-size:17px}

.floorplan{left:65px;top:17px;width:468px;height:372px;background:var(--plan);border:1px solid #cfcfcf}
.brand-side{left:22px;top:372px;transform-origin:0 0;transform:rotate(-90deg);display:flex;align-items:center;gap:8px;font-size:16px;color:#3a3a3a;white-space:nowrap}
.brand-side .brand-dot{background:var(--red)}

.more{left:0;top:418px;width:326px;height:308px;background:var(--red);color:var(--white)}
.more-head{height:28px;background:var(--black);width:323px;font-family:"Montserrat",sans-serif;font-weight:800;font-size:17px;line-height:28px;padding-left:22px;letter-spacing:.3px}
.more-list{list-style:none;padding:12px 10px 0 14px;font-size:7.5px;line-height:10px}
.more-list>li{position:relative;padding-left:10px;margin-bottom:5px}
.more-list>li::before{content:"";position:absolute;left:0;top:2px;border:3px solid transparent;border-left:5px solid var(--white)}
.contact-box{display:inline-block;border:1px solid var(--white);padding:1px 8px;margin:4px 0 0 9px;font-weight:900;font-style:italic;font-size:8.4px}
.suites{list-style:none;margin-top:2px}
.suites li{position:relative;padding-left:10px;margin-top:3px}
.suites li::before{content:"";position:absolute;left:1px;top:2px;width:4px;height:2px;border-left:1px solid var(--white);border-bottom:1px solid var(--white);transform:rotate(-45deg)}
.amenities{padding-left:24px;font-size:7.5px;line-height:13.6px}
.amenities h3{font-size:10px;font-weight:700;margin-bottom:1px}
.amenities ol{list-style:none;padding-left:9px}

.office-photo{left:326px;top:418px;width:235px;height:189px;background:linear-gradient(170deg,#c3a56c,#7a5a3e 55%,#3e2e26)}
.contact-panel{left:326px;top:607px;width:235px;height:119px;background:var(--black);color:var(--white)}
.contact-row{position:absolute;left:15px;display:flex;align-items:center;gap:15px}
.icon-sq{width:25px;height:25px;background:var(--red);display:flex;align-items:center;justify-content:center}
.contact-row .txt{font-size:9.5px;font-weight:700;line-height:12px}
.contact-row .phone{font-size:14px;font-weight:700}
</style>
</head>
<body>

<!-- Front side -->
<section class="page page--front">
  <svg class="front-shapes" viewBox="0 0 696 900" preserveAspectRatio="none">
    <defs>
      <linearGradient id="officeTone" x1="0" y1="0" x2="0.6" y2="1">
        <stop offset="0" stop-color="#c7a86a"/>
        <stop offset="0.55" stop-color="#7c5b40"/>
        <stop offset="1" stop-color="#4a3429"/>
      </linearGradient>
    </defs>
    <polygon points="0,0 696,0 696,85 365,372 0,259" fill="url(#officeTone)" role="img" aria-label="Photo of a furnished executive office with conference table and arched window"/>
    <polygon points="0,180 60,178 0,259" fill="var(--red)"/>
    <polygon points="696,85 365,372 696,550" fill="var(--red)"/>
    <polygon points="0,827 470,827 520,900 0,900" fill="var(--black)"/>
    <polygon points="500,877 696,877 696,900 520,900" fill="var(--red)"/>
  </svg>

  <div class="abs brand-front"><span class="brand-dot"></span>Northgate Realty</div>

  <div class="abs headline">
    <div class="kicker">FOR SUBLEASE</div>
    <div class="name">HALE</div>
    <div class="sub">ROAD CENTRE</div>
  </div>
  <p class="abs address">4810 Hale Road, Harbor Springs, FL 33410</p>

  <div class="thumb" style="left:20px;top:409px" role="img" aria-label="Photo of a private office with desk"></div>
  <div class="thumb" style="left:177px;top:409px" role="img" aria-label="Photo of an office with desk by the window"></div>
  <div class="thumb" style="left:20px;top:526px" role="img" aria-label="Photo of a small office with desk and artwork"></div>
  <div class="thumb" style="left:177px;top:526px" role="img" aria-label="Photo of an office with window view"></div>

  <div class="abs about"><div class="small">ABOUT THE</div><div class="big">PROPERTY</div></div>
  <ul class="abs facts">
    <li>Name of Building: <b>Hale Road Centre</b></li>
    <li>Address: <b>4810 Hale Road, Harbor Springs, FL 33410</b></li>
    <li>Building Size: <b>18,325 SF</b></li>
    <li>Vacant SF: <b>3,791 SF</b></li>
    <li>Occupancy: <b>79%</b></li>
    <li>Rental Rate: <b>$32.00/SF</b> plus suite electric</li>
    <li class="note">No extra operating expenses.</li>
  </ul>

  <div class="abs foot-contact">
    <svg width="9" height="12" viewBox="0 0 9 12"><path d="M4.5 0A4.5 4.5 0 0 0 0 4.5C0 8 4.5 12 4.5 12S9 8 9 4.5A4.5 4.5 0 0 0 4.5 0Zm0 6.3a1.8 1.8 0 1 1 0-3.6 1.8 1.8 0 0 1 0 3.6Z" fill="#fff"/></svg>
    <div>Dorran Companies<br>4810 Hale Road, Suite 110<br>Harbor Springs, FL 33410</div>
  </div>
  <div class="abs foot-phone">
    <svg width="9" height="15" viewBox="0 0 9 15"><rect x="0.8" y="0.8" width="7.4" height="13.4" rx="1.4" fill="none" stroke="#fff" stroke-width="1.4"/><circle cx="4.5" cy="11.8" r="0.9" fill="#fff"/></svg>
    561.555.0142
  </div>
</section>

<!-- Back side -->
<section class="page page--back">
  <div class="abs floorplan" role="img" aria-label="Floor plan of Suite 100 (top) and Suite 120 (bottom) with offices, conference room and stairs"></div>
  <div class="abs brand-side"><span class="brand-dot"></span>Northgate Realty</div>

  <div class="abs more">
    <h2 class="more-head">MORE ABOUT THE PROPERTY</h2>
    <ul class="more-list">
      <li>Very easy to show as landlord is in the building. For leasing information, please contact:<br>
        <span class="contact-box">Mark Dorran at 561-555-0176 or mark@dorrancompanies.com</span></li>
      <li>The Hale Road Centre is a beautiful Class A building situation in the heart of Harbor Springs but without the crazy boulevard traffic.</li>
      <li>Hale Road Centre is located directly on I-95 just off of Hale Road. The massive, new Linden development south entrance is being built across the street. The building is very convenient to restaurants, shopping, and every other trade needed.</li>
      <li>The suites are incredibly well appointed and move-in ready with custom oak doors and millwork, 10' ceilings, floor to ceiling windows</li>
      <li>Two suites are available, which can be combined for 3,791 SF in total.
        <ul class="suites">
          <li>Suite 120 is available right now and is 1,488 SF with 1 large executive office, 2 smaller offices, a conference room, break room, and reception area.</li>
          <li>Suite 100 is available in February 2019, but could be vacated sooner. Suite 120 is 2,303 SF and has 6 offices, break room, reception area, and a very large meeting room.</li>
        </ul>
      </li>
    </ul>
    <div class="amenities">
      <h3>Features &amp; Amenities:</h3>
      <ol>
        <li>a. Plenty of parking</li>
        <li>b. On-site management</li>
        <li>c. Some furniture available if needed.</li>
      </ol>
    </div>
  </div>

  <div class="abs office-photo" role="img" aria-label="Photo of the executive office with conference table and arched window"></div>

  <div class="abs contact-panel">
    <div class="contact-row" style="top:14px">
      <span class="icon-sq"><svg width="10" height="14" viewBox="0 0 9 12"><path d="M4.5 0A4.5 4.5 0 0 0 0 4.5C0 8 4.5 12 4.5 12S9 8 9 4.5A4.5 4.5 0 0 0 4.5 0Zm0 6.3a1.8 1.8 0 1 1 0-3.6 1.8 1.8 0 0 1 0 3.6Z" fill="#fff"/></svg></span>
      <span class="txt">Dorran Companies<br>4810 Hale Road, Suite 110<br>Harbor Springs, FL 33410</span>
    </div>
    <div class="contact-row" style="top:51px">
      <span class="icon-sq"><svg width="9" height="15" viewBox="0 0 9 15"><rect x="0.8" y="0.8" width="7.4" height="13.4" rx="1.4" fill="none" stroke="#fff" stroke-width="1.4"/><circle cx="4.5" cy="11.8" r="0.9" fill="#fff"/></svg></span>
      <span class="phone">561.555.0142</span>
    </div>
    <div class="contact-row" style="top:84px">
      <span class="icon-sq"><svg width="15" height="15" viewBox="0 0 16 16"><circle cx="8" cy="8" r="6.8" fill="none" stroke="#fff" stroke-width="1.4"/><path d="M1.2 8h13.6M8 1.2c2.2 2 2.2 11.6 0 13.6M8 1.2c-2.2 2-2.2 11.6 0 13.6" fill="none" stroke="#fff" stroke-width="1.1"/></svg></span>
      <span class="txt">http://www.dorrancompanies.com</span>
    </div>
  </div>
</section>

</body>
</html>
```